Marlowe Crest Realty business card design

Looking for an upscale and clean business card design and updated logo. I sell to a very high-end south Florida real estate market.
Target Market(s)
High-end real estate in south Florida real estate market
Industry/Entity Type
Real Estate Agent
Contact Information for Business Card
Marlowe Crest Realty, Inc
738 West Pinecrest Ave, Suite 410/510, Fort Lauderdale, FL 33308
Gary Whitlock - Broker/Owner
954-327-8846 Direct
garyshomes@quellmail.com
Website: DwellTarrowBay.com
Font styles to use
Other font styles liked:
- Copperplate Gothic, Georgia, etc.
Requirements
Must have
- My photo, company name, my name and title, all info stated in Details above
Nice to have
- Luxury home design element, waterfront

```html
<!DOCTYPE html>
<html lang="en">
<head>
<meta charset="utf-8">
<title>Marlowe Crest Realty – Business Card</title>
<link href="https://fonts.googleapis.com/css2?family=Cormorant+Garamond:wght@500&family=Michroma&family=Open+Sans:wght@400&display=swap" rel="stylesheet">
<style>
  :root {
    --backdrop: #2a2a2a;
    --card: #ffffff;
    --ink: #1c1c1c;
    --muted: #333333;
    --gold: #f2c230;
    --night: #000000;
    --photo-top: #e9e4da;
    --photo-bottom: #c9bfae;
  }
  html, body {
    margin: 0;
    width: 1200px;
    height: 1015px;
    overflow: hidden;
    background: radial-gradient(circle at 50% 45%, #3a3a3a 0%, var(--backdrop) 70%);
  }
  .sheet { position: relative; width: 1200px; height: 1015px; }
  .card {
    position: absolute;
    left: 290px;
    width: 620px;
    height: 354px;
    background: var(--card);
    overflow: hidden;
    box-shadow: 0 10px 30px rgba(0,0,0,.5);
  }
  .card--front { top: 110px; }
  .card--back { top: 524px; }

  .brand {
    position: absolute;
    display: flex;
    align-items: center;
    gap: 14px;
    font-family: "Cormorant Garamond", Georgia, serif;
    font-weight: 500;
    color: var(--ink);
    white-space: nowrap;
  }
  .brand__dot { border-radius: 50%; background: var(--gold); flex: none; }
  .card--front .brand { left: 50%; top: 50%; transform: translate(-50%, -50%); font-size: 34px; }
  .card--front .brand__dot { width: 56px; height: 56px; }
  .card--back .brand { left: 30px; top: 62px; font-size: 21px; gap: 10px; }
  .card--back .brand__dot { width: 36px; height: 36px; }

  .portrait {
    position: absolute;
    left: 76px;
    top: 118px;
    width: 78px;
    height: 94px;
    border-radius: 4px;
    background: linear-gradient(180deg, var(--photo-top), var(--photo-bottom));
    border: 2px solid var(--gold);
  }

  .divider {
    position: absolute;
    left: 352px;
    top: 34px;
    width: 1px;
    height: 190px;
    background: var(--ink);
  }
  .contact {
    position: absolute;
    left: 372px;
    top: 30px;
    width: 236px;
    font-family: "Open Sans", Arial, sans-serif;
    color: var(--muted);
  }
  .contact__name {
    font-family: "Michroma", Arial, sans-serif;
    font-weight: 400;
    color: var(--gold);
    font-size: 14px;
    letter-spacing: 2.5px;
    margin: 0;
    white-space: nowrap;
  }
  .contact__title { font-size: 10.5px; margin: 2px 0 18px; }
  .contact__list { list-style: none; margin: 0; padding: 0; font-size: 10.5px; line-height: 1.35; }
  .contact__list li { display: flex; align-items: flex-start; gap: 8px; margin-bottom: 8px; }
  .contact__list svg { width: 13px; height: 13px; flex: none; margin-top: 1px; fill: var(--gold); }
  .wave { position: absolute; inset: 0; }
</style>
</head>
<body>
<main class="sheet">
  <section class="card card--front" aria-label="Card front">
    <div class="brand"><span class="brand__dot"></span>Marlowe Crest Realty, Inc</div>
  </section>

  <section class="card card--back" aria-label="Card back">
    <svg class="wave" viewBox="0 0 620 354" aria-hidden="true">
      <path d="M0 354 L0 350 C150 318 250 262 380 270 C500 278 560 220 620 168 L620 354 Z" fill="var(--night)"/>
      <path d="M0 336 C150 300 250 246 380 254 C500 262 560 204 620 152" fill="none" stroke="var(--gold)" stroke-width="3"/>
    </svg>

    <div class="brand"><span class="brand__dot"></span>Marlowe Crest Realty, Inc</div>
    <div class="portrait" role="img" aria-label="Portrait photo of Gary Whitlock, Broker/Owner"></div>
    <div class="divider"></div>

    <div class="contact">
      <h2 class="contact__name">GARY WHITLOCK</h2>
      <p class="contact__title">Broker/Owner</p>
      <ul class="contact__list">
        <li><svg viewBox="0 0 16 16"><path d="M3 1l3 3-1.5 2a9 9 0 0 0 5.5 5.5L12 10l3 3-2 2C7 15 1 9 1 3z"/></svg>954-327-8846 Direct</li>
        <li><svg viewBox="0 0 16 16"><path d="M1 3h14v10H1zM2 4l6 5 6-5v-.5H2z" fill-rule="evenodd"/></svg>garyshomes@quellmail.com</li>
        <li><svg viewBox="0 0 16 16"><path d="M8 1a7 7 0 1 0 0 14A7 7 0 0 0 8 1zm0 1.5c1 1 1.7 2.7 1.9 4.5H6.1C6.3 5.2 7 3.5 8 2.5zM2.6 7h2.1c.1-1.5.5-2.9 1.1-4A5.5 5.5 0 0 0 2.6 7zm8.7 0h2.1a5.5 5.5 0 0 0-3.2-4c.6 1.1 1 2.5 1.1 4zM2.6 9a5.5 5.5 0 0 0 3.2 4c-.6-1.1-1-2.5-1.1-4zm3.5 0c.2 1.8.9 3.5 1.9 4.5 1-1 1.7-2.7 1.9-4.5zm5.2 0c-.1 1.5-.5 2.9-1.1 4a5.5 5.5 0 0 0 3.2-4z"/></svg>DwellTarrowBay.com</li>
        <li><svg viewBox="0 0 16 16"><path d="M8 1a5 5 0 0 0-5 5c0 4 5 9 5 9s5-5 5-9a5 5 0 0 0-5-5zm0 3a2 2 0 1 1 0 4 2 2 0 0 1 0-4z"/></svg><span>738 West Pinecrest Ave<br>Suite 410/510, Fort Lauderdale<br>FL 33308</span></li>
      </ul>
    </div>
  </section>
</main>
</body>
</html>
```